Alapca breeding needs a website

Presentation of the farm, animals (stallions, mares, information about the animals, for sale) and possible later expansion with a webshop (alpaca wool products). We want to present our farm and the animals on the farm on this page. A mission why we are doing this. Furthermore, each animal should be shown with a picture and described. Later we want to sell our own products made from alpaca wool via a webshop. But we still need to grow a bit to do that.

Target Market(s)

Information about my alpaca breeding and the alpaca farm

Industry/Entity Type

Tierzucht

Number of Pages Required

1 page

Font styles to use
Sans Serif

Requirements
Must have
• Modern design that matches the logo
Nice to have
• Intuitive operation / Clear structure
Should not have
• No

```html
<!DOCTYPE html>
<html lang="en">
<head>
<meta charset="utf-8">
<title>Alta Vista Alpacas</title>
<link href="https://fonts.googleapis.com/css2?family=Cinzel:wght@700;800&family=Open+Sans:wght@400;600;700&display=swap" rel="stylesheet">
<style>
:root{
  --navy:#0c2547;
  --navy-deep:#0a1f3d;
  --green:#84c341;
  --green-dark:#6fae2e;
  --white:#ffffff;
  --text:#444b55;
  --muted:#5f6670;
  --light:#f3f3ef;
}
*{box-sizing:border-box;margin:0;padding:0}
html,body{width:1200px;height:4494px;overflow:hidden}
body{position:relative;font-family:"Open Sans",sans-serif;color:var(--text);background:var(--white)}
.abs{position:absolute}
.serif{font-family:"Cinzel",serif;font-weight:800;color:var(--navy)}
.btn{position:absolute;display:flex;align-items:center;justify-content:center;border-radius:22px;font-weight:700;text-decoration:none}
.btn-navy{background:var(--navy);color:var(--green)}
.btn-green{background:var(--green);color:var(--navy)}
.rule{position:absolute;height:2px}

/* header */
.topbar{left:0;top:0;width:1200px;height:87px;background:var(--navy);border-top:3px solid var(--green)}
.nav a{position:absolute;top:38px;color:#fff;font-size:13px;text-decoration:none}
.brand-plate{left:509px;top:0;width:182px;height:188px;background:#fff;border-radius:0 0 36px 36px;display:flex;flex-direction:column;align-items:center;justify-content:center;gap:8px}
.brand-dot{width:38px;height:38px;border-radius:50%;background:var(--green)}
.brand-name{font-family:"Cinzel",serif;font-weight:800;color:var(--navy);font-size:22px;text-align:center;line-height:1.1}
.icon-btn{top:31px;width:28px;height:28px;border-radius:50%;background:var(--green)}

/* hero */
.hero-photo{left:0;top:87px;width:1200px;height:747px;background:linear-gradient(180deg,#cfdcea 0%,#dde6ee 30%,#a9b9a0 48%,#6d9a3a 62%,#5a8a2b 100%)}
.hero-title{left:0;top:230px;width:1200px;text-align:center;font-size:52px}
.hero-text{left:220px;top:300px;width:760px;text-align:center;font-size:18px;line-height:33px;color:#1d2530}

/* products */
.section-title{left:0;width:1200px;text-align:center;font-size:42px}
.product{position:absolute;top:975px;width:220px;text-align:center}
.product-photo{width:220px;height:220px;border-radius:50%;margin:0 auto;box-shadow:6px 6px 0 var(--green),0 8px 24px rgba(0,0,0,.15)}
.product h3{font-family:"Cinzel",serif;font-weight:800;color:#111;font-size:19px;margin-top:42px}
.product p{font-size:11.5px;line-height:20px;color:var(--muted);margin-top:8px}
.product .btn{position:relative;margin:18px auto 0;width:108px;height:32px;font-size:12px}
.arrow{top:1160px;width:24px;height:24px}

/* mares */
.mares-photo{left:0;top:1587px;width:593px;height:572px;background:linear-gradient(90deg,#a55a22 0%,#b8682a 55%,rgba(132,195,65,0) 100%)}
.body-white{color:#fff;font-size:13.5px;line-height:27px}

/* about alpaca */
.pill{border-radius:122px}
.body-dark{font-size:13.5px;line-height:27px;color:var(--muted)}

/* contact */
.field{position:absolute;background:#fff;border-radius:26px;color:#555;font-size:16px;padding-left:34px;display:flex;align-items:center}
</style>
</head>
<body>

<!-- header -->
<header class="abs topbar"></header>
<nav class="nav">
  <a class="abs" style="left:110px">HOME</a>
  <a class="abs" style="left:217px">ABOUT US</a>
  <a class="abs" style="left:348px">OUR ANIMALS</a>
  <a class="abs" style="left:749px">PRODUCTS</a>
  <a class="abs" style="left:886px">CONTACT US</a>
</nav>
<svg class="abs icon-btn" style="left:990px" viewBox="0 0 28 28"><circle cx="14" cy="14" r="14" fill="#84c341"/><circle cx="13" cy="13" r="4" fill="none" stroke="#0c2547" stroke-width="2"/><line x1="16" y1="16" x2="19" y2="19" stroke="#0c2547" stroke-width="2"/></svg>
<svg class="abs icon-btn" style="left:1024px" viewBox="0 0 28 28"><circle cx="14" cy="14" r="14" fill="#84c341"/><path d="M14 19l-5-5a3 3 0 015-4 3 3 0 015 4z" fill="#0c2547"/></svg>
<svg class="abs icon-btn" style="left:1058px" viewBox="0 0 28 28"><circle cx="14" cy="14" r="14" fill="#84c341"/><path d="M8 9h2l2 7h7l1-5h-9" fill="none" stroke="#0c2547" stroke-width="2"/><circle cx="13" cy="19" r="1.3" fill="#0c2547"/><circle cx="18" cy="19" r="1.3" fill="#0c2547"/></svg>

<!-- hero -->
<div class="abs hero-photo" role="img" aria-label="Herd of alpacas on a green pasture under a pale sky"></div>
<svg class="abs" style="left:0;top:715px" width="1200" height="125" viewBox="0 0 1200 125" preserveAspectRatio="none"><path d="M0 120 Q600 -40 1200 120 V125 H0 Z" fill="#fff"/><path d="M0 120 Q600 -40 1200 120" fill="none" stroke="#84c341" stroke-width="4"/></svg>
<div class="abs brand-plate"><div class="brand-dot"></div><div class="brand-name">ALTA VISTA<br>ALPACAS</div></div>
<h1 class="abs serif hero-title">WELCOME TO ALTA VISTA ALPACAS</h1>
<p class="abs hero-text">Sed ut perspiciatis unde omnis iste natus error sit voluptatem accusantium doloremque laudantium, totam rem aperiam, eaque ipsa quae ab illo inventore veritatis et</p>
<a class="btn btn-green" style="left:443px;top:380px;width:147px;height:42px;font-size:16px">Get Started</a>
<a class="btn btn-navy" style="left:607px;top:380px;width:148px;height:42px;font-size:16px">Buy Products</a>

<!-- shop -->
<h2 class="abs serif section-title" style="top:818px">SHOP OUR PRODUCTS</h2>
<div class="rule" style="left:520px;top:888px;width:160px;background:linear-gradient(90deg,transparent,var(--green),transparent)"></div>
<p class="abs" style="left:0;top:910px;width:1200px;text-align:center;font-size:16px;color:var(--muted)">Sed ut perspiciatis unde omnis iste natus error sit voluptatem accusantium doloremque laudantium</p>
<svg class="abs arrow" style="left:52px" viewBox="0 0 24 24"><circle cx="12" cy="12" r="11" fill="#fff" stroke="#ccc" stroke-width="1.5"/><path d="M13 7l-5 5 5 5M8 12h9" fill="none" stroke="#ccc" stroke-width="2"/></svg>
<svg class="abs arrow" style="left:1122px" viewBox="0 0 24 24"><circle cx="12" cy="12" r="11" fill="#0a1a2f"/><path d="M11 7l5 5-5 5M16 12H7" fill="none" stroke="#fff" stroke-width="2"/></svg>

<div class="product" style="left:113px"><div class="product-photo" role="img" aria-label="Stack of colourful woven wool scarves" style="background:linear-gradient(135deg,#3b74b8,#c4486a,#2d5fa2)"></div><h3>Wool Scarf</h3><p>Lorem ipsum dolor sit amet, con<br>tetur adipiscing elit, sed do eiusmod te<br>mpor incididunt ut labo</p><a class="btn btn-navy">Shop Now</a></div>
<div class="product" style="left:364px"><div class="product-photo" role="img" aria-label="Pile of fluffy woolen alpaca toys" style="background:linear-gradient(135deg,#e9e4dc,#cfc6b8,#b9ad9a)"></div><h3>Woolen Toys</h3><p>Lorem ipsum dolor sit amet, con<br>tetur adipiscing elit, sed do eiusmod te<br>mpor incididunt ut labo</p><a class="btn btn-navy">Shop Now</a></div>
<div class="product" style="left:615px"><div class="product-photo" role="img" aria-label="Brightly coloured knitted bags" style="background:linear-gradient(135deg,#d93a6b,#2f7fd0,#e8b52a)"></div><h3>Bags</h3><p>Lorem ipsum dolor sit amet, con<br>tetur adipiscing elit, sed do eiusmod te<br>mpor incididunt ut labo</p><a class="btn btn-navy">Shop Now</a></div>
<div class="product" style="left:867px"><div class="product-photo" role="img" aria-label="Skeins of red alpaca yarn" style="background:linear-gradient(135deg,#a8363c,#8a2a30,#b84a4d)"></div><h3>Thread</h3><p>Lorem ipsum dolor sit amet, con<br>tetur adipiscing elit, sed do eiusmod te<br>mpor incididunt ut labo</p><a class="btn btn-navy">Shop Now</a></div>

<!-- mares -->
<svg class="abs" style="left:0;top:1430px" width="1200" height="729" viewBox="0 0 1200 729" preserveAspectRatio="none"><path d="M0 0 Q600 190 1200 0 V729 H0 Z" fill="#84c341"/></svg>
<div class="abs mares-photo" role="img" aria-label="Chestnut mare standing with her foal"></div>
<h2 class="abs serif" style="left:656px;top:1676px;font-size:42px">OUR MARES</h2>
<div class="rule" style="left:656px;top:1748px;width:175px;background:var(--navy)"></div>
<p class="abs body-white" style="left:656px;top:1768px;width:490px">I must explain to you how all this mistaken idea of denouncing pleasure and praising pain was born and I will give you a complete account of the system, and expound the actual teachings of the great explorer of the truth, the master-builder of human happiness.</p>
<p class="abs body-white" style="left:656px;top:1904px;width:490px">No one rejects, dislikes, or avoids pleasure itself, because it is pleasure, but because those who do not know how to pursue pleasure rationally encounter consequences that are extremely painful.</p>
<a class="btn btn-navy" style="left:656px;top:2016px;width:120px;height:38px;font-size:13px">Buy Here</a>

<!-- about alpaca -->
<h2 class="abs serif" style="left:91px;top:2325px;font-size:42px">ABOUT ALPACA</h2>
<div class="rule" style="left:91px;top:2397px;width:175px;background:linear-gradient(90deg,var(--green),transparent)"></div>
<p class="abs body-dark" style="left:91px;top:2421px;width:410px">I must explain to you how all this mistaken idea of denouncing pleasure and praising pain was born and I will give you a complete account of the system, and expound the actual teachings of the great explorer</p>
<p class="abs body-dark" style="left:91px;top:2556px;width:410px">No one rejects, dislikes, or avoids pleasure itself, because it is pleasure, but because those who do not know how to pursue pleasure rationally encounter</p>
<a class="btn btn-navy" style="left:91px;top:2665px;width:118px;height:38px;font-size:13px">Buy Here</a>
<div class="abs pill" style="left:584px;top:2290px;width:243px;height:410px;background:linear-gradient(180deg,#3d8fd0 0%,#7aa8c8 35%,#b8a98c 65%,#8a7a55 100%)" role="img" aria-label="Two white alpacas against a blue sky"></div>
<div class="abs pill" style="left:844px;top:2339px;width:244px;height:410px;background:linear-gradient(180deg,#a7a396 0%,#c9c1b0 35%,#9c7450 70%,#6f5a3e 100%)" role="img" aria-label="Large herd of alpacas in a mountain valley"></div>

<!-- stallions -->
<div class="abs" style="left:0;top:2839px;width:1200px;height:672px;background:var(--light)"></div>
<div class="abs" style="left:118px;top:2938px;width:458px;height:458px;border-radius:50%;border-right:6px solid var(--green);border-top:6px solid transparent;border-bottom:6px solid transparent"></div>
<div class="abs" style="left:113px;top:2938px;width:454px;height:454px;border-radius:50%;border:5px solid #fff;background:linear-gradient(135deg,#8c6a48 0%,#6e4d30 45%,#6c8c3c 100%)" role="img" aria-label="Two brown stallions standing in a paddock"></div>
<h2 class="abs serif" style="left:633px;top:2972px;font-size:42px">ABOUT STALLIONS</h2>
<div class="rule" style="left:633px;top:3042px;width:175px;background:linear-gradient(90deg,var(--green),transparent)"></div>
<p class="abs body-dark" style="left:633px;top:3069px;width:460px">I must explain to you how all this mistaken idea of denouncing pleasure and praising pain was born and I will give you a complete account of the system, and expound the actual teachings of the great explorer</p>
<p class="abs body-dark" style="left:633px;top:3175px;width:460px">No one rejects, dislikes, or avoids pleasure itself, because it is pleasure, but because those who do not know how to pursue pleasure rationally encounter consequences that are extremely painful. Nor again is there anyone who loves o</p>
<a class="btn btn-navy" style="left:633px;top:3312px;width:119px;height:38px;font-size:13px">Buy Here</a>

<!-- contact -->
<div class="abs" style="left:0;top:3511px;width:1200px;height:983px;background:linear-gradient(180deg,var(--navy) 0%,var(--navy-deep) 100%)"></div>
<h2 class="abs serif section-title" style="top:3602px;color:#fff">GET IN TOUCH WITH US</h2>
<div class="rule" style="left:520px;top:3675px;width:160px;background:linear-gradient(90deg,transparent,var(--green),transparent)"></div>
<div class="field" style="left:200px;top:3727px;width:388px;height:51px">Full Name</div>
<div class="field" style="left:200px;top:3799px;width:388px;height:51px">Email Address</div>
<div class="field" style="left:200px;top:3871px;width:388px;height:51px">Contact Number</div>
<div class="btn btn-green" style="left:200px;top:3943px;width:388px;height:51px;border-radius:26px;font-size:17px">Submit Here</div>
<div class="field" style="left:612px;top:3727px;width:388px;height:267px;border-radius:24px;align-items:flex-start;padding-top:20px">Message</div>

<!-- footer -->
<svg class="abs" style="left:0;top:4060px" width="1200" height="434" viewBox="0 0 1200 434" preserveAspectRatio="none"><path d="M0 130 Q600 -120 1200 130 V434 H0 Z" fill="#fff"/></svg>
<div class="abs" style="left:0;top:4130px;width:1200px;display:flex;flex-direction:column;align-items:center;gap:14px">
  <div class="brand-dot" style="width:54px;height:54px"></div>
  <div class="brand-name" style="font-size:38px">ALTA VISTA ALPACAS</div>
</div>
<div class="abs" style="left:0;top:4362px;width:1200px;text-align:center;font-size:13px;color:var(--navy);word-spacing:2px">HOME &nbsp;&nbsp;&nbsp;&nbsp;&nbsp;&nbsp;|&nbsp;&nbsp;&nbsp;&nbsp;&nbsp;&nbsp; ABOUT US &nbsp;&nbsp;&nbsp;&nbsp;&nbsp;&nbsp;|&nbsp;&nbsp;&nbsp;&nbsp;&nbsp;&nbsp; OUR ANIMALS &nbsp;&nbsp;&nbsp;&nbsp;&nbsp;&nbsp;|&nbsp;&nbsp;&nbsp;&nbsp;&nbsp;&nbsp; PRODUCTS &nbsp;&nbsp;&nbsp;&nbsp;&nbsp;&nbsp;|&nbsp;&nbsp;&nbsp;&nbsp;&nbsp;&nbsp; CONTACT US</div>
<div class="abs" style="left:536px;top:4408px;width:34px;height:34px;border-radius:50%;background:var(--green)"></div>
<div class="abs" style="left:583px;top:4408px;width:34px;height:34px;border-radius:50%;background:var(--green)"></div>
<div class="abs" style="left:628px;top:4408px;width:34px;height:34px;border-radius:50%;background:var(--green)"></div>
<p class="abs" style="left:0;top:4458px;width:1200px;text-align:center;font-size:10.5px;color:var(--muted)">(C) Copyright 2024 | All Rights Reserved</p>
<div class="abs" style="left:0;top:4490px;width:1200px;height:4px;background:var(--green)"></div>

</body>
</html>
```